Velvette by Marisa Dunn business cards

I am after a business card that will fit the name of my business - velvette.
I want something classy and sexy and nothing tacky.
Ideas that I like are Zebra print backgrounds glitter back grounds
Two ideas I had were
1. Zebra print in black and white, the name Velvette by Marisa Dunn and a shilouette of a woman laying on top of the name. Or instead of zebra a glitter background.
2. Idea very similar except for instead of a woman a pair of lips maybe a hot pink glitter or a gold glitter depending on background with the business name between the lips.
Or you can do something completely different.

```html
<!DOCTYPE html>
<html lang="en">
<head>
<meta charset="utf-8">
<title>Velvette by Marisa Dunn — Business Cards</title>
<link rel="stylesheet" href="https://fonts.googleapis.com/css2?family=Didact+Gothic&family=Montserrat:wght@700&display=swap">
<style>
  :root {
    --bg: #e4e4e4;
    --card: #f7f7f7;
    --card-shade: #e9e9e9;
    --ink: #3a3a3a;
    --ink-dark: #1f1f1f;
    --stripe: #4a4a4a;
    --stripe-light: #d8d8d8;
  }
  html, body {
    margin: 0;
    padding: 0;
    width: 1200px;
    height: 873px;
    overflow: hidden;
    background: var(--bg);
  }
  .canvas {
    position: relative;
    width: 1200px;
    height: 873px;
    display: flex;
    justify-content: center;
    align-items: center;
    gap: 90px;
  }
  .card {
    position: relative;
    width: 340px;
    height: 580px;
    background: radial-gradient(circle at 50% 40%, var(--card) 40%, var(--card-shade) 100%);
    box-shadow: 0 6px 18px rgba(0,0,0,0.18);
    overflow: hidden;
    font-family: "Didact Gothic", sans-serif;
    color: var(--ink);
  }

  /* Front */
  .brand {
    position: absolute;
    left: 0;
    right: 0;
    top: 150px;
    display: flex;
    flex-direction: column;
    align-items: center;
    gap: 26px;
  }
  .brand-square {
    width: 96px;
    height: 96px;
    background: var(--stripe);
  }
  .brand-name {
    font-family: "Didact Gothic", sans-serif;
    font-size: 34px;
    line-height: 1.15;
    letter-spacing: 2px;
    text-align: center;
    color: var(--ink);
  }

  /* Back */
  .holder {
    position: absolute;
    left: 28px;
    top: 56px;
    width: 260px;
  }
  .holder-name {
    font-family: "Montserrat", sans-serif;
    font-weight: 700;
    font-size: 22px;
    color: var(--ink-dark);
    margin: 0;
  }
  .holder-rule {
    height: 4px;
    margin: 3px 0 2px;
    background: linear-gradient(90deg, var(--ink-dark) 0%, var(--ink-dark) 40%, rgba(31,31,31,0) 100%);
  }
  .holder-title {
    font-size: 18px;
    margin: 0;
    color: var(--ink);
  }
  .contact {
    position: absolute;
    right: 26px;
    top: 140px;
    text-align: right;
    font-size: 16px;
    line-height: 31px;
    color: var(--ink);
  }
  .contact p { margin: 0; }
  .contact .email { margin-top: 38px; }
  .stripe-band {
    position: absolute;
    left: 0;
    bottom: 0;
    width: 340px;
    height: 250px;
  }
</style>
</head>
<body>
  <main class="canvas">
    <section class="card card-front" aria-label="Card front">
      <div class="brand">
        <div class="brand-square"></div>
        <div class="brand-name">Velvette<br>by Marisa Dunn</div>
      </div>
    </section>

    <section class="card card-back" aria-label="Card back">
      <header class="holder">
        <h1 class="holder-name">Marisa Dunn</h1>
        <div class="holder-rule"></div>
        <p class="holder-title">Proprietor</p>
      </header>
      <address class="contact" style="font-style:normal">
        <p>12, Larkspur Ave</p>
        <p>Glendale, CA 91205</p>
        <p>555014276</p>
        <p>555019834</p>
        <p class="email">velvettebymd@velvettebymd.com</p>
      </address>
      <svg class="stripe-band" viewBox="0 0 340 250" role="img" aria-label="Black and white zebra print band">
        <defs>
          <linearGradient id="band-tone" x1="0" y1="0" x2="1" y2="1">
            <stop offset="0" stop-color="#5a5a5a"/>
            <stop offset="0.5" stop-color="#8a8a8a"/>
            <stop offset="1" stop-color="#4a4a4a"/>
          </linearGradient>
        </defs>
        <polygon points="340,20 340,250 0,250 0,120" fill="url(#band-tone)"/>
      </svg>
    </section>
  </main>
</body>
</html>
```